Pawn & Gun store business card design

Hello! We would like a new business card design for our pawn & gun store. We loan money on items of value and sell firearms, jewelry, electronics & more.

Card will need to have the following information:

Business name - Prairie Nickel Pawn & Gun
Address - 2417 Hwy 53 S. Suite C Wylie, TX 75246
Employees name - Darren Kellum
Phone number - 972-613-8840
Email - PrairieNickelPawn@Mailvera.com
Website - PrairieNickelPawn.com

Somewhere on the card we would like it to say "Offering 10 Month Layaway!" & "We buy & loan on anything of value!". Our main store color is orange (please see logo). Logo does not have to be on the business card but it can be. Would like the back to have an area to write a note on the back. We like vintage things like old coins, collectables, firearms and more so think about this in the design. We want a business card as unique as our store!

Colors

Designer to choose colors to be used in the design.

Requirements
Nice to have
• Vintage Style

```html
<!DOCTYPE html>
<html lang="en">
<head>
<meta charset="utf-8">
<title>Prairie Nickel Pawn &amp; Gun – Business Card</title>
<link href="https://fonts.googleapis.com/css2?family=Roboto+Slab:wght@400;700&family=Roboto:wght@400&display=swap" rel="stylesheet">
<style>
  :root {
    --bg: #8c8c8c;
    --paper: #f1efeb;
    --brown: #4a2a1e;
    --brown-soft: #6b4a3c;
    --flourish: #cdbfb6;
    --orange: #d4601e;
    --ink: #5a5a5a;
    --rule: #d9d6d1;
    --divider: #b8b5b0;
  }
  * { box-sizing: border-box; margin: 0; padding: 0; }
  html, body { width: 1200px; height: 960px; overflow: hidden; background: var(--bg); }
  .card {
    position: absolute; width: 560px; height: 320px;
    background: var(--paper);
    box-shadow: 0 6px 18px rgba(0,0,0,.25);
  }

  /* Back */
  .card-back { left: 70px; top: 110px; }
  .back-frame {
    position: absolute; left: 26px; top: 26px; width: 508px; height: 264px;
    border: 2px solid var(--brown);
  }
  .note-lines { position: absolute; left: 56px; width: 448px; top: 60px; }
  .note-line { height: 30px; border-bottom: 1px solid var(--rule); }
  .frame-mark {
    position: absolute; left: 272px; top: 19px; width: 16px; height: 16px;
    transform: rotate(45deg);
    background: var(--paper); border: 2px solid var(--brown);
  }
  .flourish {
    position: absolute; width: 50px; height: 12px;
    background: var(--flourish); border-radius: 6px;
  }
  .flourish-left { left: 32px; top: 298px; }
  .flourish-right { left: 474px; top: 262px; }
  .guns-art {
    position: absolute; left: 208px; top: 262px; width: 90px; height: 40px;
    background: linear-gradient(var(--brown-soft), var(--brown)); border-radius: 6px;
  }
  .tagline {
    position: absolute; top: 282px; height: 15px;
    font-family: 'Roboto Slab', serif; font-size: 10.5px; line-height: 15px;
    color: var(--brown); background: var(--paper);
    padding: 0 6px; white-space: nowrap;
  }
  .tagline-left { left: 42px; }
  .tagline-right { left: 306px; }

  /* Front */
  .card-front { left: 570px; top: 530px; }
  .brand {
    position: absolute; left: 30px; top: 128px; width: 235px;
    display: flex; align-items: center; gap: 10px;
    font-family: 'Roboto Slab', serif; font-weight: 700; font-size: 20px; color: var(--orange);
    white-space: nowrap;
  }
  .brand-dot { width: 20px; height: 20px; border-radius: 50%; background: var(--orange); flex: none; }
  .divider { position: absolute; left: 275px; top: 70px; height: 180px; border-left: 1px solid var(--divider); }
  .details {
    position: absolute; left: 295px; top: 70px; width: 250px;
    font-family: 'Roboto', sans-serif; color: var(--ink); font-size: 13px; line-height: 1.45;
  }
  .person-name {
    font-family: 'Roboto Slab', serif; font-weight: 700; font-size: 19px;
    color: var(--orange); letter-spacing: .5px; margin-bottom: 6px;
  }
  .address { margin-bottom: 12px; }
  .contact { list-style: none; }
  .contact li { display: flex; align-items: center; gap: 8px; white-space: nowrap; }
  .contact svg { width: 11px; height: 11px; fill: var(--orange); flex: none; }
</style>
</head>
<body>

<section class="card card-back" aria-label="Card back with note area">
  <div class="back-frame"></div>
  <div class="frame-mark"></div>
  <div class="note-lines">
    <div class="note-line"></div><div class="note-line"></div><div class="note-line"></div>
    <div class="note-line"></div><div class="note-line"></div><div class="note-line"></div>
  </div>
  <div class="flourish flourish-left" role="img" aria-label="Vintage scroll flourish"></div>
  <div class="flourish flourish-right" role="img" aria-label="Vintage scroll flourish"></div>
  <p class="tagline tagline-left">Offering 10 Month Layaway</p>
  <div class="guns-art" role="img" aria-label="Two crossed vintage revolvers"></div>
  <p class="tagline tagline-right">We buy &amp; loan on anything of value</p>
</section>

<section class="card card-front" aria-label="Card front">
  <div class="brand"><span class="brand-dot"></span>Prairie Nickel Pawn</div>
  <div class="divider"></div>
  <div class="details">
    <h1 class="person-name">DARREN KELLUM</h1>
    <p class="address">Prairie Nickel Pawn &amp; Gun<br>2417 Hwy 53 S.<br>Suite C Wylie, TX 75246</p>
    <ul class="contact">
      <li><svg viewBox="0 0 24 24"><path d="M6.6 10.8a15 15 0 0 0 6.6 6.6l2.2-2.2c.3-.3.7-.4 1-.2 1.1.4 2.3.6 3.6.6.6 0 1 .4 1 1V20c0 .6-.4 1-1 1A17 17 0 0 1 3 4c0-.6.4-1 1-1h3.5c.6 0 1 .4 1 1 0 1.3.2 2.5.6 3.6.1.3 0 .7-.2 1z"/></svg>972-613-8840</li>
      <li><svg viewBox="0 0 24 24"><path d="M2 5h20v14H2zM3 6l9 7 9-7"/></svg>PrairieNickelPawn@Mailvera.com</li>
      <li><svg viewBox="0 0 24 24"><circle cx="12" cy="12" r="10"/></svg>www.PrairieNickelPawn.com</li>
    </ul>
  </div>
</section>

</body>
</html>
```